Rosko Tamblin

I am a songwriter and would like to include a bio, pictures, discography, CD covers and access to some of my music

Target Market(s)

Music Lovers, songwriters publishers

Coding

Coded - Design and coding required

Number of Pages Required

5+ page

Requirements
Must have
• Pictures of my CD covers, pictures of me and either my Music or links to my music
Nice to have
Should not have
• cartoons

```html
<!DOCTYPE html>
<html lang="en">
<head>
<meta charset="utf-8">
<title>Rosko Tamblin — Song Writer</title>
<link rel="stylesheet" href="https://fonts.googleapis.com/css2?family=Pirata+One&family=Roboto:ital,wght@0,400;0,500;0,700;1,400&display=swap">
<style>
:root{
  --orange:#f7891f;
  --orange-deep:#ef6c00;
  --cream:#f4ecd9;
  --cream-dark:#e6d8b8;
  --brown:#2b1b0e;
  --ink:#2a2018;
  --text:#3d3328;
  --white:#ffffff;
}
*{box-sizing:border-box;margin:0;padding:0}
html,body{width:1200px;height:4673px;overflow:hidden}
body{position:relative;font-family:"Roboto",Arial,sans-serif;color:var(--text);
  background:linear-gradient(90deg,var(--cream-dark) 0%,var(--cream) 30%,#f8f2e4 60%,var(--cream-dark) 100%)}
.abs{position:absolute}
.display{font-family:"Pirata One",serif;font-weight:400;letter-spacing:1px}
.btn{position:absolute;display:flex;align-items:center;justify-content:center;border-radius:30px;
  font:700 15px "Roboto",Arial,sans-serif;text-transform:uppercase;color:var(--white);background:var(--orange)}
.btn--outline{background:transparent;border:2px solid var(--orange);color:var(--orange)}
.section-title{position:absolute;left:0;width:1200px;text-align:center;font-family:"Pirata One",serif;font-size:58px;color:var(--ink);line-height:1}
.squiggle{display:block;margin:8px auto 0}

/* header */
.site-header{position:absolute;left:0;top:0;width:1200px;height:80px;z-index:5;border-bottom:1px solid rgba(255,255,255,.15)}
.logo{position:absolute;left:104px;top:18px;font-family:"Pirata One",serif;font-size:36px;color:var(--white)}
.nav{position:absolute;right:100px;top:32px;display:flex;gap:42px;font-size:14px;color:#cfc6bc}
.nav .active{color:var(--white);font-weight:500;border-bottom:2px solid var(--white);padding-bottom:10px}

/* hero */
.hero{position:absolute;left:0;top:0;width:1200px;height:760px;
  background:radial-gradient(ellipse at 30% 55%,#e2521a 0%,#9a2a0c 30%,#3b0e06 60%,#120604 85%)}
.hero-photo{position:absolute;left:500px;top:80px;width:420px;height:680px;
  background:linear-gradient(180deg,rgba(120,90,70,.55) 0%,rgba(205,198,188,.6) 40%,rgba(40,30,24,.6) 100%)}
.hero-name{left:104px;top:262px;font-size:46px;color:var(--white)}
.hero-role{left:104px;top:312px;font-size:78px;color:var(--white)}
.hero-dots{left:573px;top:656px;display:flex;gap:6px}
.hero-dots span{width:15px;height:15px;border-radius:50%;background:var(--white)}
.hero-dots span:first-child{background:transparent;border:2px solid var(--white)}

/* bio */
.bio-photo{position:absolute;left:76px;top:840px;width:432px;height:432px;border-radius:50%;border:10px solid var(--orange);
  background:radial-gradient(circle at 50% 45%,#e9e4d8 0%,#b88a55 55%,#7a5631 100%)}
.bio-title{left:588px;top:850px;font-size:62px;color:var(--ink);line-height:1}
.bio-text{left:590px;top:958px;width:500px;font-size:16px;line-height:27px;color:var(--text)}

/* cds */
.cd{position:absolute;top:1450px;width:300px;text-align:center}
.cd-art{position:relative;width:290px;height:210px;margin:0 auto}
.cd-disc{position:absolute;right:0;top:10px;width:190px;height:190px;border-radius:50%;background:#d9d9d9}
.cd-cover{position:absolute;left:20px;top:0;width:200px;height:205px;box-shadow:4px 6px 12px rgba(0,0,0,.35)}
.cd-name{margin-top:46px;font-weight:500;font-size:20px;color:var(--ink)}
.cd-desc{margin-top:6px;font-size:14px;line-height:18px}
.arrow{position:absolute;top:1535px}

/* discography */
.dark-band{position:absolute;left:0;top:1850px;width:1200px;height:630px;background:var(--brown)}
.piano{position:absolute;left:390px;top:1870px;width:810px;height:605px;
  background:radial-gradient(ellipse at 70% 30%,rgba(120,60,200,.5) 0%,rgba(40,120,200,.35) 20%,transparent 45%),
  linear-gradient(160deg,transparent 40%,#6b5646 60%,#1a1512 80%)}
.disco-box{position:absolute;left:103px;top:1969px;width:517px;height:366px;background:rgba(90,64,30,.88);border-radius:4px}
.disco-title{left:163px;top:2005px;font-size:52px;color:var(--white);line-height:1}
.disco-text{left:163px;top:2085px;width:430px;font-size:15px;line-height:27px;color:#eee3d3}

/* reviews */
.quote{left:220px;top:2675px;width:820px;text-align:center;font-style:italic;font-size:21px;line-height:35px;color:var(--text)}
.qmark{font-family:Georgia,serif;font-size:100px;color:var(--orange);font-weight:700;line-height:1}
.reviewer{left:0;width:1200px;text-align:center}
.dots{display:flex;gap:4px;justify-content:center}
.dots span{width:12px;height:12px;border-radius:50%;background:var(--ink)}
.dots span:first-child{background:transparent;border:1.5px solid var(--ink)}

/* music */
.music-title{left:121px;top:3015px;font-size:58px;color:var(--ink);line-height:1}
.tile{position:absolute;width:244px;height:214px;border-radius:4px;overflow:hidden;box-shadow:0 4px 10px rgba(0,0,0,.35)}
.tile-play{position:absolute;left:20px;top:100px;width:58px;height:58px}
.tile-label{position:absolute;left:22px;top:170px;font-size:12px;font-weight:700;color:var(--white);z-index:2;white-space:nowrap}
.tile-sub{display:block;font-weight:400;font-size:11px}
.tile-bars{position:absolute;right:6px;bottom:0}
.music-photo{position:absolute;left:707px;top:2955px;width:493px;height:816px;border-radius:420px 0 0 420px;
  background:linear-gradient(120deg,#1c1c1c 0%,#5a5a5a 45%,#2a2a2a 100%)}

/* blogs */
.blog{position:absolute;top:3938px;width:306px;height:386px;background:var(--white);box-shadow:0 4px 14px rgba(0,0,0,.2)}
.blog-img{height:210px}
.blog-body{padding:30px 34px 0}
.blog-title{font-size:16px;font-weight:700;color:var(--ink)}
.blog-text{margin-top:10px;font-size:13px;line-height:20px}
.blog .btn{position:relative;margin-top:16px;width:124px;height:34px;font-size:11px}

/* footer */
.site-footer{position:absolute;left:0;top:4384px;width:1200px;height:289px;background:var(--brown)}
.footer-nav{position:absolute;left:0;top:104px;width:1200px;display:flex;justify-content:center;gap:52px;font-size:14px;font-weight:700;color:var(--white)}
.copyright{position:absolute;left:0;top:147px;width:1200px;text-align:center;font-size:15px;color:#d6cbbd}
.social{position:absolute;left:0;top:200px;width:1200px;display:flex;justify-content:center;gap:26px}
.social span{width:20px;height:20px;border-radius:50%;background:var(--white)}
</style>
</head>
<body>

<section class="hero">
  <div class="hero-photo" role="img" aria-label="Photo of the songwriter standing before a glowing fire at night"></div>
</section>

<header class="site-header">
  <div class="logo">Rosko Tamblin</div>
  <nav class="nav">
    <span class="active">ABOUT ME</span><span>MY MUSIC</span><span>BLOG</span><span>GALLERY</span><span>MY CD'S</span><span>CONTACT</span>
  </nav>
</header>

<div class="abs display hero-name">Rosko Tamblin</div>
<div class="abs display hero-role">Song Writer</div>
<div class="btn" style="left:104px;top:427px;width:177px;height:48px;">My Music</div>
<div class="abs hero-dots"><span></span><span></span><span></span></div>

<svg class="abs" style="left:0;top:660px" width="1200" height="140" viewBox="0 0 1200 140">
  <path d="M0 100 C300 20 700 60 900 50 C1050 42 1150 10 1200 0 L1200 20 C1100 50 1000 78 800 82 C500 88 250 40 0 120Z" fill="var(--orange)"/>
  <path d="M0 120 C250 50 500 95 800 90 C1000 86 1100 50 1200 35 L1200 140 L0 140Z" fill="#f4ecd9"/>
</svg>

<!-- bio -->
<div class="bio-photo" role="img" aria-label="Portrait of the songwriter in a white shirt holding a hat"></div>
<div class="abs display bio-title">My Bio</div>
<svg class="abs" style="left:594px;top:912px" width="80" height="14"><path d="M2 8 C20 0 40 14 78 4" stroke="var(--orange)" stroke-width="3" fill="none"/></svg>
<p class="abs bio-text">Rosko Tamblin was born and raised in Houston, Texas. He began playing music at the age of eight when his sister returned home from summer camp and asked her parents to buy her a baritone ukulele. She taught her younger brother some chords on the ukulele and he was hooked. The following spring, they went to one of the border towns in Mexico and bought a Mexican guitar for $12. They restrung it with nylon strings and Tamblin began to learn how to play the guitar</p>
<div class="btn btn--outline" style="left:584px;top:1202px;width:163px;height:46px;font-size:14px;">Learn More</div>

<!-- cds -->
<div class="section-title" style="top:1330px">My Music CD's
  <svg class="squiggle" width="90" height="14"><path d="M2 8 C20 0 45 14 88 4" stroke="var(--orange)" stroke-width="3" fill="none"/></svg>
</div>
<svg class="abs arrow" style="left:70px" width="20" height="30"><path d="M14 5 L5 15 L14 25" stroke="#111" stroke-width="4" fill="none"/></svg>
<svg class="abs arrow" style="left:1124px" width="20" height="30"><path d="M6 5 L15 15 L6 25" stroke="var(--orange-deep)" stroke-width="4" fill="none"/></svg>

<div class="cd" style="left:93px">
  <div class="cd-art"><div class="cd-disc"></div><div class="cd-cover" role="img" aria-label="Colourful album cover of a man with a guitar" style="background:linear-gradient(135deg,#e23b8a,#f0c23a 50%,#3fa7d6)"></div></div>
  <div class="cd-name">THE HARBOR KIDS</div>
  <div class="cd-desc">omnis iste natus error sit voluptatem accusantium doloremque</div>
</div>
<div class="cd" style="left:445px">
  <div class="cd-art"><div class="cd-disc"></div><div class="cd-cover" role="img" aria-label="Dark album cover with a stormy sky" style="background:linear-gradient(180deg,#2b3140,#6a6d88 45%,#1a1612 80%,#a33b1a)"></div></div>
  <div class="cd-name">QUIET WEATHER</div>
  <div class="cd-desc">omnis iste natus error sit voluptatem accusantium doloremque</div>
</div>
<div class="cd" style="left:793px">
  <div class="cd-art"><div class="cd-disc"></div><div class="cd-cover" role="img" aria-label="Album cover of a fiery table scene" style="background:linear-gradient(135deg,#e8541a,#f4a32a 40%,#e9e2d4 70%,#5b4a36)"></div></div>
  <div class="cd-name">PAPER LANTERNS</div>
  <div class="cd-desc">omnis iste natus error sit voluptatem accusantium doloremque</div>
</div>

<!-- discography -->
<svg class="abs" style="left:0;top:1780px" width="1200" height="100" viewBox="0 0 1200 100">
  <path d="M0 60 C300 90 700 110 1000 50 C1100 30 1160 10 1200 0 L1200 100 L0 100Z" fill="var(--brown)"/>
  <path d="M900 75 C1000 55 1120 25 1200 0 L1200 20 C1120 45 1020 70 900 75Z" fill="var(--orange)"/>
</svg>
<div class="dark-band"></div>
<div class="piano" role="img" aria-label="Hands playing a piano keyboard with colourful music notes"></div>
<div class="disco-box"></div>
<div class="abs display disco-title">Discography</div>
<svg class="abs" style="left:163px;top:2062px" width="90" height="14"><path d="M2 8 C20 0 45 14 88 4" stroke="var(--orange)" stroke-width="3" fill="none"/></svg>
<p class="abs disco-text">Tamblin stopped listening to or playing music from the late 80s into the mid-nineties, when the singer songwriter movement began.Intrigued by the sound of these artists, he began to write again. In the past he played almost exclusively electric guitar but during</p>
<div class="btn" style="left:163px;top:2238px;width:163px;height:46px;">Learn More</div>
<svg class="abs" style="left:0;top:2440px" width="1200" height="90" viewBox="0 0 1200 90">
  <path d="M0 0 L1200 0 L1200 10 C900 40 500 20 0 60Z" fill="var(--brown)"/>
  <path d="M0 60 C500 20 900 40 1200 10 L1200 25 C900 55 500 40 0 85Z" fill="var(--orange)"/>
</svg>

<!-- reviews -->
<div class="section-title" style="top:2565px">Reviews
  <svg class="squiggle" width="90" height="14"><path d="M2 8 C20 0 45 14 88 4" stroke="var(--orange)" stroke-width="3" fill="none"/></svg>
</div>
<div class="abs qmark" style="left:155px;top:2650px">&ldquo;</div>
<p class="abs quote">At this point I have developed a continuous creative relationship with Rosko and have recorded on approximately 30 songs of his. He writes well-structured songs that allow me to flex my creative muscles. Rosko knows how to make his original ideas blossom into fully constructed arrangements that sound great</p>
<div class="abs qmark" style="left:905px;top:2780px">&rdquo;</div>
<div class="abs reviewer" style="top:2832px;font-weight:700;font-size:19px;color:var(--ink)">MARCO VELANI,</div>
<div class="abs reviewer" style="top:2862px;font-size:19px">Lowline Studio</div>
<div class="abs dots" style="left:0;top:2920px;width:1200px"><span></span><span></span><span></span></div>

<!-- music -->
<div class="music-photo" role="img" aria-label="Black and white photo of the songwriter in a hat with a vinyl record"></div>
<div class="abs display music-title">My Music</div>
<svg class="abs" style="left:125px;top:3078px" width="90" height="14"><path d="M2 8 C20 0 45 14 88 4" stroke="var(--orange)" stroke-width="3" fill="none"/></svg>

<div class="tile" style="left:121px;top:3127px;background:linear-gradient(160deg,#4a5a78,#1f2633)" role="img" aria-label="Stormy sky track artwork">
  <svg class="tile-play" viewBox="0 0 58 58"><circle cx="29" cy="29" r="29" fill="#fff"/><path d="M23 18 L40 29 L23 40Z" fill="#111"/></svg>
  <div class="tile-label">FOREST FOR TREE CD<span class="tile-sub">Listen now</span></div>
  <svg class="tile-bars" width="84" height="80"><g fill="var(--orange)"><rect x="0" y="50" width="4" height="30"/><rect x="8" y="35" width="4" height="45"/><rect x="16" y="55" width="4" height="25"/><rect x="24" y="20" width="4" height="60"/><rect x="32" y="40" width="4" height="40"/><rect x="40" y="10" width="4" height="70"/><rect x="48" y="30" width="4" height="50"/><rect x="56" y="45" width="4" height="35"/><rect x="64" y="25" width="4" height="55"/><rect x="72" y="50" width="4" height="30"/><rect x="80" y="38" width="4" height="42"/></g></svg>
</div>
<div class="tile" style="left:401px;top:3127px;background:linear-gradient(180deg,#3c4a48,#1a2422)" role="img" aria-label="Misty forest track artwork">
  <svg class="tile-play" viewBox="0 0 58 58"><circle cx="29" cy="29" r="29" fill="#fff"/><path d="M23 18 L40 29 L23 40Z" fill="#111"/></svg>
  <div class="tile-label">FOREST FOR TREE CD<span class="tile-sub">Listen now</span></div>
  <svg class="tile-bars" width="84" height="80"><g fill="#fff"><rect x="0" y="50" width="4" height="30"/><rect x="8" y="35" width="4" height="45"/><rect x="16" y="55" width="4" height="25"/><rect x="24" y="20" width="4" height="60"/><rect x="32" y="40" width="4" height="40"/><rect x="40" y="10" width="4" height="70"/><rect x="48" y="30" width="4" height="50"/><rect x="56" y="45" width="4" height="35"/><rect x="64" y="25" width="4" height="55"/><rect x="72" y="50" width="4" height="30"/><rect x="80" y="38" width="4" height="42"/></g></svg>
</div>
<div class="tile" style="left:116px;top:3376px;background:linear-gradient(180deg,#3e4a3a,#20281f)" role="img" aria-label="Ship at sea track artwork">
  <svg class="tile-play" viewBox="0 0 58 58"><circle cx="29" cy="29" r="29" fill="#fff"/><path d="M23 18 L40 29 L23 40Z" fill="#111"/></svg>
  <div class="tile-label">FOREST FOR TREE CD<span class="tile-sub">Listen now</span></div>
  <svg class="tile-bars" width="84" height="80"><g fill="var(--orange-deep)"><rect x="0" y="50" width="4" height="30"/><rect x="8" y="35" width="4" height="45"/><rect x="16" y="55" width="4" height="25"/><rect x="24" y="20" width="4" height="60"/><rect x="32" y="40" width="4" height="40"/><rect x="40" y="10" width="4" height="70"/><rect x="48" y="30" width="4" height="50"/><rect x="56" y="45" width="4" height="35"/><rect x="64" y="25" width="4" height="55"/><rect x="72" y="50" width="4" height="30"/><rect x="80" y="38" width="4" height="42"/></g></svg>
</div>
<div class="tile" style="left:397px;top:3376px;background:linear-gradient(180deg,#5b6a70,#2b3536 60%,#4a3a22)" role="img" aria-label="Mountain lake track artwork">
  <svg class="tile-play" viewBox="0 0 58 58"><circle cx="29" cy="29" r="29" fill="#fff"/><path d="M23 18 L40 29 L23 40Z" fill="#111"/></svg>
  <div class="tile-label">FOREST FOR TREE CD<span class="tile-sub">Listen now</span></div>
  <svg class="tile-bars" width="84" height="80"><g fill="var(--orange)"><rect x="0" y="50" width="4" height="30"/><rect x="8" y="35" width="4" height="45"/><rect x="16" y="55" width="4" height="25"/><rect x="24" y="20" width="4" height="60"/><rect x="32" y="40" width="4" height="40"/><rect x="40" y="10" width="4" height="70"/><rect x="48" y="30" width="4" height="50"/><rect x="56" y="45" width="4" height="35"/><rect x="64" y="25" width="4" height="55"/><rect x="72" y="50" width="4" height="30"/><rect x="80" y="38" width="4" height="42"/></g></svg>
</div>
<div class="btn" style="left:109px;top:3631px;width:191px;height:50px;">View All Music</div>

<!-- blogs -->
<div class="section-title" style="top:3832px">My Blogs
  <svg class="squiggle" width="90" height="14"><path d="M2 8 C20 0 45 14 88 4" stroke="var(--orange)" stroke-width="3" fill="none"/></svg>
</div>
<article class="blog" style="left:127px">
  <div class="blog-img" role="img" aria-label="Black and white photo of a guitarist in a hat" style="background:linear-gradient(135deg,#dcdcdc,#3a3a3a 60%,#111)"></div>
  <div class="blog-body">
    <div class="blog-title">AVOLUPTATEM ACCUSANTIUM</div>
    <div class="blog-text">omnis iste natus error sit voluptatem accusantium doloremque</div>
    <div class="btn btn--outline">Learn More</div>
  </div>
</article>
<article class="blog" style="left:457px">
  <div class="blog-img" role="img" aria-label="Guitarist performing on a purple lit stage" style="background:linear-gradient(160deg,#2a1a5a,#7a2a8a 50%,#1b1230)"></div>
  <div class="blog-body">
    <div class="blog-title">LABORE ET DOLORE</div>
    <div class="blog-text">omnis iste natus error sit voluptatem accusantium doloremque</div>
    <div class="btn btn--outline">Learn More</div>
  </div>
</article>
<article class="blog" style="left:785px">
  <div class="blog-img" role="img" aria-label="Glowing music notes on a dark blue background" style="background:linear-gradient(160deg,#0c1a3a,#1e3a6a 50%,#c98a2a)"></div>
  <div class="blog-body">
    <div class="blog-title">NIHIL MOLESTIAEUM</div>
    <div class="blog-text">omnis iste natus error sit voluptatem accusantium doloremque</div>
    <div class="btn btn--outline">Learn More</div>
  </div>
</article>

<footer class="site-footer">
  <nav class="footer-nav"><span>HOME</span><span>ABOUT ME</span><span>MY MUSIC</span><span>BLOG</span><span>GALLERY</span><span>CONTACT</span></nav>
  <div class="copyright">&copy; 2019-2020 Rosko Tamblin</div>
  <div class="social"><span aria-label="Photo sharing profile"></span><span aria-label="Social profile"></span><span aria-label="Microblog profile"></span></div>
</footer>

</body>
</html>
```